Business Card Design Project

Basic business card with minimal details. I just need company name, email & web address, telephone and my name.
I would like the back of the card to be grey with my logo & company name centred.

Target Market(s)

Architects
Builders
Property Developers

Industry/Entity Type

Business

Font styles to use
Sans Serif

Colors

Designer to choose colors to be used in the design.

Requirements
Must have
• Tallow Crest
Rupert Hazelby - Director
M: 0427 915203
E: rupert@tallowcrest.com.au
W: www.tallowcrest.com.au
Should not have
• No other images or pictures

```html
<!DOCTYPE html>
<html lang="en">
<head>
<meta charset="utf-8">
<title>Tallow Crest – Business Card</title>
<link href="https://fonts.googleapis.com/css2?family=Arimo:wght@400;700&display=swap" rel="stylesheet">
<style>
  :root {
    --backdrop: #e6e7e9;
    --card: #ffffff;
    --crimson: #c8213f;
    --crimson-bright: #e42d55;
    --crimson-deep: #a81c36;
    --slate: #5d7384;
    --slate-text: #4b6275;
    --steel-light: #8ea7bc;
  }
  * { box-sizing: border-box; margin: 0; padding: 0; }
  html, body {
    width: 1200px; height: 900px; overflow: hidden;
    background: var(--backdrop);
    font-family: "Arimo", Arial, sans-serif;
  }
  .card {
    position: absolute; left: 50px; top: 134px;
    width: 1100px; height: 632px;
    background: var(--card);
    box-shadow: 0 6px 24px rgba(0,0,0,0.18);
    overflow: hidden;
  }
  .brand {
    position: absolute; left: 96px; top: 118px;
    display: flex; align-items: center; gap: 34px;
  }
  .brand-square {
    width: 84px; height: 84px; background: var(--crimson);
  }
  .brand-name {
    font-size: 70px; font-weight: 400; letter-spacing: 3px;
    color: var(--slate); text-transform: uppercase; line-height: 1;
  }
  .person { position: absolute; left: 96px; top: 318px; }
  .person-name {
    font-size: 38px; font-weight: 700; color: var(--crimson);
    text-transform: uppercase; letter-spacing: 0.5px; line-height: 1;
  }
  .person-role {
    font-size: 21px; color: var(--slate-text); margin-top: 6px;
  }
  .contacts {
    position: absolute; left: 96px; top: 445px;
    list-style: none;
  }
  .contact {
    display: flex; align-items: center; height: 37px;
    font-size: 25px; color: var(--slate-text);
  }
  .contact-icon { width: 30px; height: 26px; margin-right: 26px; flex: none; }
  .footer-band { position: absolute; left: 0; bottom: 0; width: 1100px; height: 54px; }
</style>
</head>
<body>
  <main class="card">
    <div class="brand">
      <div class="brand-square"></div>
      <h1 class="brand-name">Tallow Crest</h1>
    </div>

    <div class="person">
      <h2 class="person-name">Rupert Hazelby</h2>
      <p class="person-role">Director</p>
    </div>

    <ul class="contacts">
      <li class="contact">
        <svg class="contact-icon" viewBox="0 0 30 26" aria-hidden="true">
          <path d="M2 9 Q15 0 28 9 L25 12 L21 10 L21 7 Q15 5 9 7 L9 10 L5 12 Z" fill="var(--crimson)"/>
          <path d="M8 12 L22 12 L26 24 L4 24 Z" fill="var(--crimson)"/>
          <circle cx="15" cy="18" r="3" fill="#fff"/>
        </svg>
        <span>0427 915203</span>
      </li>
      <li class="contact">
        <svg class="contact-icon" viewBox="0 0 30 26" aria-hidden="true">
          <rect x="2" y="3" width="26" height="20" fill="var(--crimson)"/>
          <path d="M3 4 L15 15 L27 4 M3 22 L12 13 M27 22 L18 13" stroke="#fff" stroke-width="2" fill="none"/>
        </svg>
        <span>rupert@tallowcrest.com.au</span>
      </li>
      <li class="contact">
        <svg class="contact-icon" viewBox="0 0 30 26" aria-hidden="true">
          <rect x="3" y="2" width="24" height="17" fill="none" stroke="var(--crimson)" stroke-width="3"/>
          <rect x="13" y="19" width="4" height="4" fill="var(--crimson)"/>
          <rect x="8" y="23" width="14" height="2.5" fill="var(--crimson)"/>
        </svg>
        <span>www.tallowcrest.com.au</span>
      </li>
    </ul>

    <svg class="footer-band" viewBox="0 0 1100 54" preserveAspectRatio="none" aria-hidden="true">
      <defs>
        <linearGradient id="band-red" x1="0" x2="1">
          <stop offset="0" stop-color="var(--crimson)"/>
          <stop offset="0.55" stop-color="var(--crimson-bright)"/>
          <stop offset="1" stop-color="var(--crimson-deep)"/>
        </linearGradient>
        <linearGradient id="band-steel" x1="0" x2="1">
          <stop offset="0" stop-color="var(--slate)"/>
          <stop offset="1" stop-color="var(--steel-light)"/>
        </linearGradient>
      </defs>
      <rect x="0" y="0" width="1100" height="54" fill="url(#band-red)"/>
      <polygon points="0,14 502,14 518,54 0,54" fill="#fff"/>
      <polygon points="0,20 486,20 500,54 0,54" fill="url(#band-steel)"/>
    </svg>
  </main>
</body>
</html>
```